TuneRoost - Music Industry App needs a top quality wordpress homepage

We need a modern responsive wordpress homepage built. Our website will only feature one page with the goal to get people to sign up to our app. A word document has been uploaded outlining the page content/sections.

Once the homepage is finalised, I will also need 2 landing pages built as part of this competition. It will be very similar to the homepage with the same layout etc but just feature different images and content. The homepage is for anyone (artists and venues) to find out about us but the landing pages will be artist or venue specific.

The completed work must be delivered as an exportable file into wordpress and be designed properly so no more work is needed to begin utilising as the actual website. The images used must be setup correctly for speed and quality also.

Target Market(s)

Venues and Artists.

Coding

Coded - Design and coding required

Requirements
Must have
• UPDATE: High Res Logo files attached
• Must be a modern looking website and be responsive. Must look good across all devices from desktop, to mobile and tablet. Needs to be very high quality.
• Please see the attached logo - I am waiting for the final high quality version and will reupload when complete but this will be enough to get you started for now. The website must have a dark base colour and have red/white elements to match the logo. The red colour used MUST match the red colour used in the logo.
• Please have a go at creating it how you think is best and provide feedback from there. I am leaving it very open to the designers so I can get the best website possible and lots of different ideas etc.

```html
<!DOCTYPE html>
<html lang="en">
<head>
<meta charset="utf-8">
<title>TuneRoost – Live Music Booking</title>
<link href="https://fonts.googleapis.com/css2?family=Roboto:wght@400;500;700&display=swap" rel="stylesheet">
<style>
:root{
  --red:#dd1219;
  --red-dark:#b80d13;
  --ink:#222;
  --muted:#444;
  --white:#fff;
  --night:#17171c;
  --grey-band:#d9d9db;
  --map:#eceeea;
  --social:#3a8ee6;
}
*{box-sizing:border-box;margin:0;padding:0}
html,body{width:1200px;height:4440px;overflow:hidden}
body{position:relative;font-family:'Roboto',sans-serif;color:var(--ink);background:var(--white)}
.abs{position:absolute}
.center{left:0;width:1200px;text-align:center}

/* hero */
.hero-photo{left:0;top:0;width:1200px;height:760px;background:radial-gradient(ellipse at 60% 30%,#8a5a3c 0%,#4a2a22 35%,#1d1216 75%)}
.main-nav{top:44px;left:0;width:1200px;height:20px;font-size:15px;color:var(--white)}
.main-nav span{position:absolute;transform:translateX(-50%);white-space:nowrap}
.main-nav .active{color:var(--red)}
.search-btn{left:1076px;top:36px;width:34px;height:34px;border-radius:50%;background:var(--social)}
.slide-arrow{top:300px}
.brand-mark{top:150px;left:525px;width:150px;height:150px;border-radius:50%;border:18px solid var(--white)}
.brand-name{top:330px;font-size:84px;font-weight:400;color:var(--white);letter-spacing:1px}
.hero-title{top:448px;font-size:40px;font-weight:700;color:var(--white)}
.hero-sub{top:510px;font-size:16px;font-weight:500;color:var(--white);letter-spacing:1.2px}
.signup{left:281px;top:560px;width:636px;height:48px;border-radius:24px;background:var(--white)}
.signup .field{position:absolute;left:20px;top:15px;font-size:15px;color:#333}
.signup .btn{position:absolute;right:0;top:0;width:246px;height:48px;border-radius:24px;background:var(--red);color:var(--white);font-size:15px;font-weight:700;text-align:center;line-height:48px}

h2.sec-title{font-size:40px;font-weight:700;color:var(--red)}

/* steps */
.step-num{width:140px;height:140px;border-radius:50%;background:var(--red);color:var(--white);font-size:56px;font-weight:700;text-align:center;line-height:140px}
.step-text{width:240px;font-size:15px;line-height:20px;text-align:center;color:var(--ink)}

/* why */
.why-photo{left:0;top:1448px;width:1200px;height:600px;background:linear-gradient(180deg,#dcdcde 0%,#d2d2d4 55%,#a8a8ac 100%)}
.why-col{width:260px}
.why-col svg{display:block}
.why-col h3{font-size:27px;font-weight:700;color:#111;margin:10px 0 8px}
.why-col p{font-size:15.5px;line-height:27px;color:#222}

/* features */
.feature-photo{background:radial-gradient(circle at 50% 40%,#ff5a2a 0%,#c01a10 40%,#3a0606 100%)}
.feature-photo.artists{background:radial-gradient(circle at 55% 45%,#c4a08a 0%,#3a5a8a 45%,#0c1a3a 100%)}
.feature h3{font-size:40px;font-weight:500;color:var(--red)}
.ticks{list-style:none;font-size:14px;line-height:27.5px;color:#222}
.ticks li{position:relative;padding-left:32px}
.ticks li svg{position:absolute;left:2px;top:7px}
.note{font-size:14px;line-height:22px;color:var(--red)}
.pill{height:46px;border-radius:23px;background:var(--red);color:var(--white);font-size:15px;font-weight:700;line-height:46px;text-align:center}

/* about */
.about-photo{left:0;top:3141px;width:1200px;height:460px;background:radial-gradient(ellipse at 75% 40%,#5a4a3a 0%,#262220 45%,#101010 100%)}
.about-title{top:3235px;font-size:38px;font-weight:500;color:var(--red)}
.about-text{left:170px;top:3322px;width:860px;text-align:center;font-size:14.5px;line-height:27.5px;color:var(--white)}

/* map + footer */
.map{left:0;top:3591px;width:1200px;height:530px;background:linear-gradient(160deg,#eef0ec 0%,#e4e8e0 60%,#d8e6cc 100%)}
.footer-name{top:4135px;font-size:60px;font-weight:400;color:var(--white)}
.footer-mark{left:560px;top:4050px;width:80px;height:80px;border-radius:50%;border:10px solid var(--white)}
.social{top:4251px;width:42px;height:42px;border-radius:50%;background:var(--social)}
.social.alt{background:var(--red)}
.footer-nav{top:4330px;left:0;width:1200px;font-size:15px;color:var(--white)}
.footer-nav span{position:absolute;transform:translateX(-50%);white-space:nowrap}
.copyright{top:4381px;font-size:12.5px;color:var(--white)}
</style>
</head>
<body>

<!-- HERO -->
<div class="abs hero-photo" role="img" aria-label="Crowd of friends celebrating at a live music night"></div>
<nav class="abs main-nav">
  <span class="active" style="left:260px">Home</span>
  <span style="left:334px">About</span>
  <span style="left:457px">How TuneRoost Works</span>
  <span style="left:615px">Why TuneRoost?</span>
  <span style="left:728px">Venues</span>
  <span style="left:817px">Artists</span>
  <span style="left:919px">Contact Us</span>
</nav>
<div class="abs search-btn">
  <svg width="34" height="34" viewBox="0 0 34 34"><circle cx="15.5" cy="15.5" r="5" fill="none" stroke="#fff" stroke-width="2.4"/><line x1="19" y1="19" x2="23" y2="23" stroke="#fff" stroke-width="2.6" stroke-linecap="round"/></svg>
</div>
<svg class="abs slide-arrow" style="left:92px" width="22" height="36" viewBox="0 0 22 36"><polyline points="18,3 4,18 18,33" fill="none" stroke="#fff" stroke-width="2.5"/></svg>
<svg class="abs slide-arrow" style="left:1086px" width="22" height="36" viewBox="0 0 22 36"><polyline points="4,3 18,18 4,33" fill="none" stroke="#fff" stroke-width="2.5"/></svg>

<div class="abs brand-mark"></div>
<div class="abs center brand-name">TuneRoost</div>
<h1 class="abs center hero-title">Rideshare for Live Music</h1>
<p class="abs center hero-sub">TuneRoost connects venues with artists to make booking gigs simple</p>
<div class="abs signup"><span class="field">ENTER EMAIL</span><span class="btn">SIGN UP NOW FOR FREE</span></div>

<svg class="abs" style="left:0;top:595px" width="1200" height="170" viewBox="0 0 1200 170">
  <polygon points="0,60 272,125 1200,5 1200,170 0,170" fill="#fff"/>
  <polygon points="0,17 272,150 760,70 272,130 0,60" fill="var(--red)"/>
</svg>

<!-- HOW IT WORKS -->
<h2 class="abs center sec-title" style="top:798px">How TuneRoost Works</h2>
<svg class="abs" style="left:0;top:900px" width="1200" height="400" viewBox="0 900 1200 400">
  <g fill="none" stroke="#222" stroke-width="2" stroke-dasharray="7 5">
    <path d="M141,1008 C155,990 170,982 186,979"/>
    <line x1="325" y1="978" x2="532" y2="978"/>
    <line x1="672" y1="978" x2="873" y2="978"/>
    <path d="M1013,978 C1150,1000 1150,1248 960,1248 L842,1248"/>
    <line x1="702" y1="1248" x2="498" y2="1248"/>
  </g>
  <circle cx="141" cy="1008" r="7" fill="var(--red)"/>
  <g fill="none" stroke="var(--red)" stroke-width="3">
    <polyline points="416,970 424,978 416,986"/>
    <polyline points="762,970 770,978 762,986"/>
    <polyline points="1074,1028 1082,1036 1090,1026"/>
    <polyline points="975,1240 967,1248 975,1256"/>
    <polyline points="603,1240 595,1248 603,1256"/>
  </g>
</svg>
<div class="abs step-num" style="left:185px;top:926px">01</div>
<div class="abs step-num" style="left:532px;top:926px">02</div>
<div class="abs step-num" style="left:873px;top:926px">03</div>
<div class="abs step-num" style="left:702px;top:1154px">04</div>
<div class="abs step-num" style="left:358px;top:1154px">05</div>
<p class="abs step-text" style="left:135px;top:1080px">Artists and venues sign up for free and create a profile</p>
<p class="abs step-text" style="left:482px;top:1080px">Venues search for an artist for their upcoming gigs</p>
<p class="abs step-text" style="left:823px;top:1080px">Venues request a quote and communicate with the artist direct</p>
<p class="abs step-text" style="left:652px;top:1308px">Upon completion the money is paid to the artist within 48 hours or less</p>
<p class="abs step-text" style="left:308px;top:1308px">The gig is booked in once payment is provided by the venue</p>

<!-- WHY -->
<div class="abs why-photo" role="img" aria-label="Audience enjoying a concert, shown in greyscale"></div>
<h2 class="abs center sec-title" style="top:1515px">Why TuneRoost?</h2>

<div class="abs why-col" style="left:76px;top:1626px">
  <svg width="86" height="62" viewBox="0 0 86 62" fill="none" stroke="#111" stroke-width="2"><rect x="62" y="14" width="20" height="42"/><circle cx="72" cy="26" r="5"/><circle cx="72" cy="44" r="7"/><path d="M4,56 V34 H58 V56"/><circle cx="14" cy="30" r="5"/><circle cx="30" cy="28" r="5"/><circle cx="46" cy="30" r="5"/><circle cx="28" cy="10" r="6"/><line x1="28" y1="0" x2="28" y2="2"/></svg>
  <h3>Simple</h3>
  <p>TuneRoost makes gig booking easy for both the venue and artist</p>
</div>
<div class="abs why-col" style="left:347px;top:1626px">
  <svg width="86" height="62" viewBox="0 0 86 62" fill="none" stroke="#111" stroke-width="2"><circle cx="43" cy="12" r="7"/><path d="M30,36 C30,24 56,24 56,36 Z"/><circle cx="20" cy="30" r="7"/><path d="M6,54 C6,42 34,42 34,54 Z"/><circle cx="66" cy="30" r="7"/><path d="M52,54 C52,42 80,42 80,54 Z"/></svg>
  <h3>Connect</h3>
  <p>Join the TuneRoost community which is full of amazing artists and venues.</p>
</div>
<div class="abs why-col" style="left:615px;top:1626px">
  <svg width="86" height="62" viewBox="0 0 86 62" fill="none" stroke="#111" stroke-width="2.2"><path d="M30,2 H58 V30 C58,44 44,54 44,58 C44,54 30,44 30,30 Z"/><line x1="44" y1="2" x2="44" y2="58"/><line x1="30" y1="28" x2="58" y2="28"/></svg>
  <h3>Protection</h3>
  <p>Everyone is protected with our complimentary dispute resolutions</p>
</div>
<div class="abs why-col" style="left:884px;top:1626px">
  <svg width="86" height="62" viewBox="0 0 86 62" fill="none" stroke="#111" stroke-width="2.2"><path d="M24,8 H44 L74,38 L54,58 L24,28 Z"/><circle cx="34" cy="18" r="4"/><path d="M34,14 C24,2 8,4 6,14"/></svg>
  <h3>Price</h3>
  <p>Get the best rate possible with TuneRoost only receiving 5% of the artists fee</p>
</div>

<svg class="abs" style="left:0;top:1900px" width="1200" height="150" viewBox="0 0 1200 150">
  <polygon points="0,55 215,140 1200,25 1200,150 0,150" fill="#fff"/>
  <polygon points="0,18 215,143 690,70 215,122 0,55" fill="var(--red)"/>
</svg>

<!-- VENUES -->
<div class="abs feature-photo" style="left:74px;top:2133px;width:512px;height:427px" role="img" aria-label="DJ performing on stage under red lights"></div>
<section class="abs feature" style="left:614px;top:2140px;width:520px">
  <h3>Venues</h3>
  <ul class="ticks" style="margin-top:14px">
    <li><svg width="16" height="13" viewBox="0 0 16 13"><polyline points="1,7 6,11 15,1" fill="none" stroke="var(--red)" stroke-width="2.6"/></svg>TuneRoost is a 100% FREE service for all venues - you pay us nothing!</li>
    <li><svg width="16" height="13" viewBox="0 0 16 13"><polyline points="1,7 6,11 15,1" fill="none" stroke="var(--red)" stroke-width="2.6"/></svg>Get instant access to hundreds of artists around your local community</li>
    <li><svg width="16" height="13" viewBox="0 0 16 13"><polyline points="1,7 6,11 15,1" fill="none" stroke="var(--red)" stroke-width="2.6"/></svg>All genres to suit any venue from a pub to a wedding or even a nightclub</li>
    <li><svg width="16" height="13" viewBox="0 0 16 13"><polyline points="1,7 6,11 15,1" fill="none" stroke="var(--red)" stroke-width="2.6"/></svg>Simple booking process with a money back guarantee</li>
    <li><svg width="16" height="13" viewBox="0 0 16 13"><polyline points="1,7 6,11 15,1" fill="none" stroke="var(--red)" stroke-width="2.6"/></svg>Communicate directly with the artist and negotiate the price</li>
  </ul>
  <p class="note" style="margin-top:18px">TuneRoost is not yet ready to host gigs as we're currently working on building our artists. We are launching for venues in Q4 2019. Pre-register now to keep informed and be one of the first people to use our platform</p>
  <div class="pill" style="width:302px;margin-top:22px">EMAIL INPUT TO PRE REGISTER</div>
</section>

<!-- ARTISTS -->
<section class="abs feature" style="left:76px;top:2625px;width:500px">
  <h3 style="margin-left:12px">Artists</h3>
  <ul class="ticks" style="margin-top:12px">
    <li><svg width="16" height="13" viewBox="0 0 16 13"><polyline points="1,7 6,11 15,1" fill="none" stroke="var(--red)" stroke-width="2.6"/></svg>Sign up to TuneRoost for FREE and get yourself in front of venues</li>
    <li><svg width="16" height="13" viewBox="0 0 16 13"><polyline points="1,7 6,11 15,1" fill="none" stroke="var(--red)" stroke-width="2.6"/></svg>Only pay us if you get a gig - we only get 5% of the fee you charge the venue</li>
    <li><svg width="16" height="13" viewBox="0 0 16 13"><polyline points="1,7 6,11 15,1" fill="none" stroke="var(--red)" stroke-width="2.6"/></svg>All genres and artists welcome - as long as you're experienced and professional</li>
    <li><svg width="16" height="13" viewBox="0 0 16 13"><polyline points="1,7 6,11 15,1" fill="none" stroke="var(--red)" stroke-width="2.6"/></svg>Get paid within 48 hours or less after the gig guaranteed!</li>
    <li><svg width="16" height="13" viewBox="0 0 16 13"><polyline points="1,7 6,11 15,1" fill="none" stroke="var(--red)" stroke-width="2.6"/></svg>Negotiate your price and don't pay huge agent fees to ensure you earn top dollar</li>
  </ul>
  <div class="pill" style="width:438px;margin-top:30px">SIGN UP AND CREATE YOUR TUNEROOST PROFILE NOW</div>
  <div class="pill" style="width:302px;margin-top:18px">EMAIL INPUT TO PRE REGISTER</div>
</section>
<div class="abs feature-photo artists" style="left:610px;top:2595px;width:512px;height:477px" role="img" aria-label="Two singers sharing a microphone on stage"></div>

<!-- ABOUT -->
<div class="abs about-photo" role="img" aria-label="Musician in a cap performing under stage lights"></div>
<h2 class="abs center about-title">About TuneRoost</h2>
<p class="abs about-text">Lorem ipsum is a pseudo-Latin text used in web design, typography, layout, and printing in place of English to emphasise design elements over content. It's also called placeholder (or filler) text. It's a convenient tool for mock-ups. It helps to outline the visual elements of a document or presentation, eg typography, font, or layout. Lorem ipsum is mostly a part of a Latin text by the classical author and philosopher Marcus Vellanus. Its words and letters have been changed by addition or removal, so to deliberately render its content nonsensical; it's not genuine, correct</p>

<!-- MAP + FOOTER -->
<div class="abs map" role="img" aria-label="Map of central Australia"></div>
<svg class="abs" style="left:0;top:4010px" width="1200" height="430" viewBox="0 0 1200 430">
  <path d="M0,78 C300,60 800,20 1200,0 V430 H0 Z" fill="var(--night)"/>
</svg>
<div class="abs footer-mark"></div>
<div class="abs center footer-name">TuneRoost</div>
<div class="abs social" style="left:457px"></div>
<div class="abs social" style="left:519px"></div>
<div class="abs social" style="left:581px"></div>
<div class="abs social alt" style="left:641px"></div>
<div class="abs social" style="left:703px"></div>
<nav class="abs footer-nav">
  <span style="left:261px">Home</span>
  <span style="left:334px">About</span>
  <span style="left:457px">How TuneRoost Works</span>
  <span style="left:615px">Why TuneRoost?</span>
  <span style="left:729px">Venues</span>
  <span style="left:818px">Artists</span>
  <span style="left:920px">Contact Us</span>
</nav>
<p class="abs center copyright">© 2019. All rights reserved. Privacy Policy</p>

</body>
</html>
```